New Business card design to reflect rebrand

I would like a business card design with a good base colour for our new logo and also a placeholder for a profile pic of the card holder. the design needs to be editable to the point that we can easily change the picture of the person and use that design for printmerlo etc. we are looking at a metalic finish business card so will need a good base colour to bring out the finish.

Target Market(s)

prospective customers

Industry/Entity Type

Business

Contact Information for Business Card

I would like one editable design that we can change the name of the card holder and profile picture. The design need to be in a format that be send to printmerlo etc.

Our address is Fenwick Lodge, Copse Lane, Farley Whitcombe, GU14 3TP Tel no. 01483 556172

Requirements
Must have
• place holder for a profile pic for the card holder. in AI or preferably PSD format

```html
<!DOCTYPE html>
<html lang="en">
<head>
<meta charset="utf-8">
<title>Corvane Workplace Services – Business Card</title>
<link rel="stylesheet" href="https://fonts.googleapis.com/css2?family=Open+Sans:wght@400;600&display=swap">
<style>
  :root {
    --page-bg: #ece9e6;
    --card-base: #2a333d;
    --card-deep: #1f262e;
    --card-sheen: #35404b;
    --accent-orange: #e8731c;
    --slate-name: #5f7589;
    --text-light: #f2f4f6;
    --photo-top: #3a4654;
    --photo-bottom: #1c2631;
  }
  * { margin: 0; padding: 0; box-sizing: border-box; }
  html, body {
    width: 1200px;
    height: 900px;
    overflow: hidden;
    background: var(--page-bg);
    font-family: "Open Sans", Arial, sans-serif;
  }
  .canvas { position: relative; width: 1200px; height: 900px; }

  .card {
    position: absolute;
    width: 556px;
    height: 342px;
    background: radial-gradient(ellipse at 60% 25%, var(--card-sheen) 0%, var(--card-base) 45%, var(--card-deep) 100%);
    overflow: hidden;
    box-shadow: 0 6px 18px rgba(0, 0, 0, 0.25);
  }
  .card--front { left: 238px; top: 62px; }
  .card--back  { left: 457px; top: 518px; width: 560px; }

  .profile-photo {
    position: absolute;
    left: 0;
    top: 0;
    width: 262px;
    height: 342px;
    background: linear-gradient(180deg, var(--photo-top) 0%, var(--photo-bottom) 100%);
  }

  .holder-name {
    position: absolute;
    right: 25px;
    top: 82px;
    font-size: 27px;
    font-weight: 600;
    letter-spacing: 0.2px;
    white-space: nowrap;
  }
  .holder-name__first { color: var(--accent-orange); }
  .holder-name__last  { color: var(--slate-name); }

  .contact {
    position: absolute;
    right: 26px;
    color: var(--text-light);
    font-size: 14px;
    line-height: 23px;
    text-align: right;
    white-space: nowrap;
  }
  .contact--direct  { top: 146px; }
  .contact--address { top: 217px; }

  .brand {
    position: absolute;
    left: 0;
    right: 0;
    top: 160px;
    text-align: center;
    color: var(--slate-name);
    font-weight: 600;
    letter-spacing: 3px;
    text-transform: uppercase;
  }
  .brand__name { font-size: 52px; line-height: 60px; }
  .brand__tagline { font-size: 21px; line-height: 30px; letter-spacing: 4px; }
</style>
</head>
<body>
<main class="canvas">
  <section class="card card--front" aria-label="Business card front">
    <div class="profile-photo" role="img" aria-label="Profile photo placeholder of the card holder"></div>
    <h1 class="holder-name">
      <span class="holder-name__first">Peter</span>
      <span class="holder-name__last">Hallam</span>
    </h1>
    <p class="contact contact--direct">01483 556172<br>info@corvane.com</p>
    <p class="contact contact--address">Fenwick Lodge, Copse Lane,<br>Farley Whitcombe, GU14 3TP</p>
  </section>

  <section class="card card--back" aria-label="Business card back">
    <div class="brand">
      <div class="brand__name">Corvane</div>
      <div class="brand__tagline">Workplace Services</div>
    </div>
  </section>
</main>
</body>
</html>
```